Business Cards - Brightpath Horizon

need to design unique business card for my mortgage business. I need to design credit card style business card for my business or any unique idea that you might have

Target Market(s)

Home Loan customers

Industry/Entity Type

Mortgage Brokerage

Contact Information for Business Card

please design credit card style or very unique style business card

Colors

Designer to choose colors to be used in the design.

Requirements
Must have
• Name
• position
• Phone number
• fax number
• email address
• website address
• social media address
• All above fields will be provided once design in finalised

```html
<!DOCTYPE html>
<html lang="en">
<head>
<meta charset="utf-8">
<title>Brightpath Horizon – Business Card</title>
<link rel="stylesheet" href="https://fonts.googleapis.com/css2?family=Roboto+Slab:wght@700&family=Share+Tech+Mono&family=Arimo:wght@400&display=swap">
<style>
  :root {
    --page-bg: #e9e6e1;
    --card-bg: #1d2228;
    --card-edge: #2a3038;
    --tree-tone: #253038;
    --accent-blue: #2ea3dc;
    --brand-blue: #1f3fc4;
    --gold: #d9b45a;
    --gold-dark: #a9802c;
    --white: #ffffff;
  }
  html, body {
    margin: 0;
    padding: 0;
    width: 1200px;
    height: 969px;
    overflow: hidden;
    background: var(--page-bg);
  }
  .card {
    position: absolute;
    left: 162px;
    top: 245px;
    width: 900px;
    height: 514px;
    border-radius: 30px;
    background: linear-gradient(160deg, var(--card-edge) 0%, var(--card-bg) 55%, #181c21 100%);
    box-shadow: 0 18px 40px rgba(0,0,0,0.25);
    overflow: hidden;
  }
  .backdrop-art {
    position: absolute;
    left: 300px;
    top: 0;
    width: 400px;
    height: 514px;
    background: radial-gradient(ellipse at 50% 45%, var(--tree-tone) 0%, rgba(37,48,56,0) 70%);
  }
  .holder {
    position: absolute;
    left: 42px;
    top: 76px;
  }
  .holder-name {
    margin: 0;
    font-family: "Roboto Slab", serif;
    font-weight: 700;
    font-size: 29px;
    color: var(--accent-blue);
    letter-spacing: 0.5px;
    line-height: 1.1;
  }
  .holder-title {
    margin: 4px 0 0;
    font-family: "Roboto Slab", serif;
    font-weight: 700;
    font-size: 21px;
    color: var(--white);
    letter-spacing: 0.5px;
  }
  .brand {
    position: absolute;
    right: 50px;
    top: 88px;
    display: flex;
    align-items: center;
    gap: 12px;
  }
  .brand-mark {
    width: 18px;
    height: 18px;
    border-radius: 50%;
    background: var(--brand-blue);
  }
  .brand-name {
    font-family: "Roboto Slab", serif;
    font-weight: 700;
    font-size: 28px;
    color: var(--brand-blue);
  }
  .card-number {
    position: absolute;
    left: 0;
    right: 0;
    top: 245px;
    text-align: center;
    font-family: "Share Tech Mono", monospace;
    font-size: 60px;
    letter-spacing: 10px;
    word-spacing: 24px;
    color: var(--gold);
    text-shadow: 0 2px 0 var(--gold-dark);
  }
  .contact {
    position: absolute;
    left: 42px;
    top: 414px;
    font-family: "Arimo", sans-serif;
    font-size: 22px;
    color: var(--white);
    line-height: 30px;
  }
  .contact p { margin: 0; }
  .social {
    position: absolute;
    left: 666px;
    top: 404px;
  }
  .website {
    position: absolute;
    right: 45px;
    top: 454px;
    font-family: "Arimo", sans-serif;
    font-size: 21px;
    letter-spacing: 1.5px;
    color: var(--accent-blue);
  }
</style>
</head>
<body>
  <main class="card" aria-label="Brightpath Horizon business card">
    <div class="backdrop-art" role="img" aria-label="Faint tree silhouette in the card background"></div>

    <section class="holder">
      <h1 class="holder-name">DANIEL REEVE</h1>
      <p class="holder-title">CEO/FOUNDER</p>
    </section>

    <div class="brand">
      <span class="brand-mark"></span>
      <span class="brand-name">Brightpath Horizon</span>
    </div>

    <div class="card-number">555 308 4162</div>

    <section class="contact">
      <p class="contact-phone">P. 555 214 7730</p>
      <p class="contact-email">hello@brightpath.com</p>
    </section>

    <svg class="social" width="190" height="44" viewBox="0 0 190 44" role="img" aria-label="Social media links">
      <circle cx="22" cy="22" r="20" fill="var(--accent-blue)"/>
      <circle cx="67" cy="22" r="20" fill="var(--accent-blue)"/>
      <circle cx="115" cy="22" r="20" fill="var(--accent-blue)"/>
      <circle cx="165" cy="22" r="20" fill="var(--accent-blue)"/>
    </svg>

    <div class="website">www.brightpath.com</div>
  </main>
</body>
</html>
```